Local fast-growing company in the service sector

We are looking for a modern business card design, which should also appear on our letterheads

Target Market(s)

Private and industrial sectors

Contact Information for Business Card

Vorname Name
Kellberger Str. 18
74129 Feldrach
Tel.: 07146-839214-0
Name@agentur-kvtl.de

Colors
9d9d9d
919191
aaaaaa

Requirements
Must have
• The logo (file) in silver

```html
<!DOCTYPE html>
<html lang="de">
<head>
<meta charset="utf-8">
<title>KVTL – Visitenkarte</title>
<link rel="stylesheet" href="https://fonts.googleapis.com/css2?family=Lato:wght@400;700;900&display=swap">
<style>
  :root {
    --page-bg: #e4e4e4;
    --card-left-top: #d6d6d6;
    --card-left-bottom: #bdbdbd;
    --card-right-top: #9d9d9d;
    --card-right-bottom: #858585;
    --divider-line: #e9e9e9;
    --divider-gap: #6f6f6f;
    --logo-ink: #5e5e5e;
    --name-ink: #ffffff;
    --role-ink: #eeeeee;
    --contact-ink: #f4f4f4;
    --icon-bg: #c4c4c4;
    --icon-ink: #8a8a8a;
    --address-ink: #555b66;
    --card-edge: #aaaaaa;
  }
  * { box-sizing: border-box; margin: 0; padding: 0; }
  html, body { width: 1200px; height: 970px; overflow: hidden; }
  body {
    background: var(--page-bg);
    font-family: "Lato", Arial, sans-serif;
    position: relative;
  }
  .business-card {
    position: absolute;
    left: 100px;
    top: 186px;
    width: 1000px;
    height: 598px;
    border: 1px solid var(--card-edge);
    display: flex;
    overflow: hidden;
    box-shadow: 0 10px 30px rgba(0,0,0,0.12);
  }
  .card-brand {
    width: 506px;
    height: 100%;
    background: linear-gradient(160deg, var(--card-left-top), var(--card-left-bottom));
    position: relative;
  }
  .brand-mark {
    position: absolute;
    left: 56px;
    top: 254px;
    display: flex;
    align-items: center;
    gap: 22px;
    color: var(--logo-ink);
  }
  .brand-square {
    width: 70px;
    height: 70px;
    background: var(--logo-ink);
  }
  .brand-name {
    font-weight: 900;
    font-size: 78px;
    letter-spacing: 2px;
    line-height: 1;
  }
  .card-divider {
    width: 30px;
    height: 100%;
    display: flex;
    background: var(--divider-gap);
  }
  .card-divider span { display: block; height: 100%; }
  .divider-line { width: 7px; background: var(--divider-line); }
  .divider-gap { width: 4px; background: var(--divider-gap); }
  .card-divider .divider-dark { width: 8px; background: var(--divider-gap); }
  .card-contact {
    flex: 1;
    height: 100%;
    background: linear-gradient(160deg, var(--card-right-top), var(--card-right-bottom));
    padding: 146px 0 0 75px;
  }
  .person-name {
    color: var(--name-ink);
    font-weight: 700;
    font-size: 27px;
    line-height: 1.2;
  }
  .person-company {
    color: var(--role-ink);
    font-size: 20px;
    margin-top: 8px;
  }
  .contact-list { list-style: none; margin-top: 48px; }
  .contact-item {
    display: flex;
    align-items: center;
    gap: 14px;
    color: var(--contact-ink);
    font-size: 22px;
    height: 34px;
    margin-bottom: 14px;
  }
  .contact-icon { width: 34px; height: 34px; flex: none; }
  .postal-address {
    margin-top: 26px;
    color: var(--address-ink);
    font-weight: 700;
    font-size: 22px;
    line-height: 42px;
    font-style: normal;
  }
</style>
</head>
<body>
  <main class="business-card">
    <section class="card-brand">
      <div class="brand-mark">
        <span class="brand-square"></span>
        <span class="brand-name">KVTL</span>
      </div>
    </section>

    <div class="card-divider" aria-hidden="true">
      <span class="divider-dark"></span>
      <span class="divider-line"></span>
      <span class="divider-gap"></span>
      <span class="divider-line"></span>
      <span class="divider-dark"></span>
    </div>

    <section class="card-contact">
      <h1 class="person-name">Marlene Voss</h1>
      <p class="person-company">Veltra Partners</p>

      <ul class="contact-list">
        <li class="contact-item">
          <svg class="contact-icon" viewBox="0 0 34 34" aria-hidden="true">
            <circle cx="17" cy="17" r="17" fill="var(--icon-bg)"/>
            <path d="M9.5 14 Q17 8.5 24.5 14 L22.5 16 L20 15 L20 13.5 Q17 12.5 14 13.5 L14 15 L11.5 16 Z" fill="var(--icon-ink)"/>
            <path d="M13 17 L21 17 L23 24 L11 24 Z" fill="var(--icon-ink)"/>
          </svg>
          <span>07146-839214-0</span>
        </li>
        <li class="contact-item">
          <svg class="contact-icon" viewBox="0 0 34 34" aria-hidden="true">
            <circle cx="17" cy="17" r="17" fill="var(--icon-bg)"/>
            <rect x="9.5" y="11.5" width="15" height="11" fill="var(--icon-ink)"/>
            <path d="M9.5 11.5 L17 18 L24.5 11.5" fill="none" stroke="var(--icon-bg)" stroke-width="1.5"/>
          </svg>
          <span>mvoss@agentur-kvtl.de</span>
        </li>
      </ul>

      <address class="postal-address">
        Kellberger Str. 18<br>
        74129 Feldrach
      </address>
    </section>
  </main>
</body>
</html>
```